Letterhead, stationery and email signature for construction business

I need the letterhead, stationery and email signature designs for a construction business. I want them to have a corporate feel to them.

I've attached the logo for reference.

```html
<!DOCTYPE html>
<html lang="en">
<head>
<meta charset="utf-8">
<title>Harlowe Builders Letterhead</title>
<link href="https://fonts.googleapis.com/css2?family=Lato:wght@400;700&family=Montserrat:wght@700&family=Parisienne&display=swap" rel="stylesheet">
<style>
  :root{
    --backdrop:#e4e4e4;
    --paper:#e2e2e2;
    --brand-blue:#2b56a3;
    --brand-blue-light:#2e63ad;
    --steel:#5b5d6b;
    --ink:#333338;
    --ink-strong:#2e2e33;
  }
  *{margin:0;padding:0;box-sizing:border-box}
  html,body{width:1153px;height:1200px;overflow:hidden;background:var(--backdrop)}
  .letterhead{
    position:absolute;left:158px;top:15px;width:836px;height:1170px;
    background:var(--paper);overflow:hidden;
    box-shadow:0 4px 18px rgba(0,0,0,.18);
    font-family:"Lato",sans-serif;color:var(--ink);
  }
  .brand{position:absolute;left:76px;top:66px;display:flex;align-items:center;gap:12px}
  .brand-square{width:62px;height:62px;background:var(--brand-blue)}
  .brand-name{font-family:"Lato",sans-serif;font-weight:700;color:var(--brand-blue);line-height:1}
  .brand-name .primary{display:block;font-size:40px;letter-spacing:.5px}
  .brand-name .secondary{display:block;font-size:17px;letter-spacing:9px;margin-top:4px}
  .contact{
    position:absolute;left:569px;top:50px;padding-left:8px;
    border-left:1.5px solid var(--brand-blue);font-style:normal;
    font-family:"Montserrat",sans-serif;font-weight:700;font-size:12.5px;color:var(--ink-strong);line-height:18px;
  }
  .contact .address{margin-bottom:8px}
  .contact .row{display:flex;align-items:center;gap:6px;height:19.5px}
  .contact svg{width:13px;height:13px;flex:none}
  .letter{position:absolute;left:64px;width:708px;top:257px;font-size:15.6px;line-height:18px}
  .date{margin-bottom:21px}
  .recipient{margin-bottom:19px}
  .company{margin-bottom:18px}
  .salutation{font-size:19.5px;font-weight:700;color:var(--ink-strong);margin-bottom:18px;line-height:24px}
  .body p{text-align:justify;margin-bottom:18px}
  .closing{margin-top:35px}
  .signature{font-family:"Parisienne",cursive;font-size:38px;color:#222;margin-top:16px;line-height:48px}
  .footer-band{
    position:absolute;left:0;bottom:0;width:836px;height:150px;
    background:linear-gradient(180deg,var(--steel) 0%,var(--brand-blue) 45%,var(--brand-blue-light) 100%);
  }
</style>
</head>
<body>
<main class="letterhead">
  <header>
    <div class="brand">
      <div class="brand-square"></div>
      <div class="brand-name"><span class="primary">HARLOWE</span><span class="secondary">BUILDERS</span></div>
    </div>
    <address class="contact">
      <div class="address">42-07 Alder Row 8,<br>Brookvale, NY 10999</div>
      <div class="row">
        <svg viewBox="0 0 16 16" aria-hidden="true"><path fill="#2b56a3" d="M2 6c0-2 3-3 6-3s6 1 6 3v1h-3V6H5v1H2zM4 8h8l2 6H2z"/></svg>
        <span>555-014-2290</span></div>
      <div class="row">
        <svg viewBox="0 0 16 16" aria-hidden="true"><rect x="1" y="3" width="14" height="10" fill="#2b56a3"/><path d="M1 3l7 6 7-6" fill="none" stroke="#e2e2e2" stroke-width="1.3"/></svg>
        <span>info@harlowebuilders.com</span></div>
      <div class="row">
        <svg viewBox="0 0 16 16" aria-hidden="true"><circle cx="8" cy="8" r="7" fill="#2b56a3"/><path d="M1 8h14M8 1c-3 3-3 11 0 14M8 1c3 3 3 11 0 14" fill="none" stroke="#e2e2e2" stroke-width="1"/></svg>
        <span>www.harlowebuilders.com</span></div>
    </address>
  </header>

  <section class="letter">
    <p class="date">Feb-03-2022</p>
    <p class="recipient">Mr, Adam Reyes<br>President</p>
    <p class="company">Northpoint Holdings<br>123 Street Name, Suite# 10<br>City, State, 120023</p>
    <p class="salutation">Dear Mr, Adam</p>
    <div class="body">
      <p>Lorem ipsum dolor sit amet, consectetur adipisicing elit, sed do eiusmod tempor incididunt ut labore et dolore magna aliqua. Ut enim ad minim veniam, quis nostrud exercitation ullamco laboris nisi ut aliquip ex ea commodo consequat. Duis aute irure dolor in reprehenderit in voluptate velit esse cillum dolore eu fugiat nulla pariatur.</p>
      <p>Lorem ipsum dolor sit amet, consectetur adipisicing elit, sed do eiusmod tempor incididunt ut labore et dolore magna aliqua. Ut enim ad minim veniam, quis nostrud exercitation ullamco laboris nisi ut aliquip ex ea commodo consequat. Duis aute irure dolor in reprehenderit in voluptate velit esse cillum dolore eu fugiat nulla pariatur.</p>
      <p>Lorem ipsum dolor sit amet, consectetur adipisicing elit, sed do eiusmod tempor incididunt ut labore et dolore magna aliqua. Ut enim ad minim veniam, quis nostrud exercitation ullamco laboris nisi ut aliquip ex ea commodo consequat.</p>
      <p>Excepteur sint occaecat cupidatat non proident, sunt in culpa qui officia deserunt mollit anim id est laborum. re et dolore magnam aliquam quaerat voluptatem.</p>
    </div>
    <p class="closing">Regards</p>
    <p class="signature">Daniel Carter</p>
  </section>

  <div class="footer-band" role="img" aria-label="Decorative blue and grey footer band"></div>
</main>
</body>
</html>
```